Home Page for a Swiss based start up company, trading Natural & Health food ingredients (B2B)

I would like to create a home page for my new start up company (Veltrana Swiss AG), the main field of activity is the trading and marketing of Natural and Health food ingredients towards the functional Food and Food supplements industry. (B2B).
Target Market : Functional Food and Food Supplement Manufacturers (B2B) based in Switzerland and Europe
The values I would like to convey are :
- sourcing of natural and health ingredients, (example : natural plant extracts, Omega 3, plant proteins, natural vitamins, vegan food ingredients...etc)
- Health & Nutritional Health
- Eco-friendly and Sustainability
- High Quality Standard in term of products and logistic services
- Trust and reliability
- Flexibility & speed to market
-Technical advice for the development of new products

The site will be translated in 3 languages (German, French, English)
Number of web pages : 5 : Home, About us, Products, Our Services, Contact

See here below attached Logo file.

Here some link of websites which can be taken as benchmark or source of inspiration
- https://quorbelix.com
- https://www.dralvimo.com/

Target Market(s)

Manufacturers of Functional Foods and Food Supplements in Switzerland and Europe (B2B)

Industry/Entity Type

B2B Trading of Natural & Health Ingredients

Coding

Number of Pages Required

Font styles to use
Sans Serif

Colors
0054AA
0677BA
7BADD7
CADEEF
E8F1F8
0094D4
00A9DD
6FCCEA
C7EBF8
E9F6FB
00AB8E
00BBA5
67D7C9
C6EFE9
E9F9F6
59FF00
82FF00
B8FF75
E3FFCB
F4FFEA
FFF300
FFF600
FEFA6F
FFFEC7
FFFEE8
FFC000
F8CF3A
FAE287
FDF2CF
FEFAEE
F0912C
F2A743
F7CA91
FBE8D2
FDF5EE
EE7325
F08F49
F5BC92
FAE3D3
FDF4ED

Requirements
Must have
• inspiration towards nature, sustainability, vegan food, functional food & beverages, food supplements, nutritional health, low carbon footprint
Should not have
• animals, chemistry, food additives

```html
<!DOCTYPE html>
<html lang="en">
<head>
<meta charset="utf-8">
<title>Veltrana Swiss AG – Natural &amp; Health Food Ingredients</title>
<link href="https://fonts.googleapis.com/css2?family=Poppins:wght@400;500;600;700&display=swap" rel="stylesheet">
<style>
:root{
  --green:#5ca63f;
  --orange:#ffa000;
  --slate:#3e5558;
  --ink:#222;
  --text:#333;
  --muted:#f3f3f3;
  --white:#fff;
  --salmon:#f7ad98;
}
*{box-sizing:border-box;margin:0;padding:0}
html,body{width:1200px;height:4534px;overflow:hidden}
body{font-family:'Poppins',sans-serif;color:var(--text);background:var(--white);position:relative}
section,header,footer{position:absolute;left:0;width:1200px}
.abs{position:absolute}
.btn{position:absolute;background:var(--orange);color:var(--white);font-weight:600;font-size:18px;display:flex;align-items:center;justify-content:center}
.photo{position:absolute}
.body-text{font-size:15px;line-height:30.5px}

/* top bar */
.topbar{top:0;height:55px;border-bottom:1px solid #e6e6e6}
.social-dot{position:absolute;top:17px;width:18px;height:18px;border-radius:50%;background:#555}
.contact{position:absolute;top:14px;font-size:16px;font-weight:500;color:var(--ink);display:flex;align-items:center;gap:10px}
.contact svg{flex:none}
.lang{position:absolute;left:1058px;top:18px;font-size:11px;color:#666;display:flex;gap:8px;align-items:center}
.lang i{display:block;width:20px;height:13px;background:#4a5d8c}

/* nav */
.nav{top:55px;height:91px;border-bottom:1px solid #eee}
.brand{position:absolute;left:74px;top:31px;font-size:24px;font-weight:600;color:var(--ink)}
.menu{position:absolute;top:38px;display:flex;font-size:15px;color:var(--ink)}
.menu a{position:absolute;white-space:nowrap;text-decoration:none;color:var(--ink)}
.menu a.active{color:var(--green)}

/* hero */
.hero{top:146px;height:641px}
.hero .photo{inset:0;background:linear-gradient(100deg,#a87d63 0%,#b5a594 30%,#708a8c 55%,#c06d58 80%,#8e9fa4 100%)}
.hero h1{position:absolute;left:0;width:1200px;top:178px;text-align:center;color:var(--white);font-size:90px;font-weight:700;line-height:1}
.hero p{position:absolute;left:0;width:1208px;top:286px;text-align:center;color:var(--white);font-size:29px;font-weight:500;line-height:41px}
.hero .btn{left:517px;top:392px;width:164px;height:46px;background:var(--green)}
.hero .dot{position:absolute;left:555px;top:590px;width:12px;height:12px;background:var(--orange)}

/* welcome */
.welcome{top:787px;height:598px}
.welcome .photo{left:74px;top:75px;width:600px;height:452px;background:linear-gradient(135deg,#5b4b4a,#9c8f83 45%,#c9c2b0 70%,#d7cf7a)}
.welcome h2,.split h2,.reviews h2{font-size:33px;font-weight:700;color:var(--ink);position:absolute}

/* split sections */
.split{height:482px}
.split .panel{position:absolute;top:0;height:482px;background:var(--green)}
.split h2{color:var(--white)}
.split .body-text{color:var(--white);position:absolute}

/* values */
.values{top:1867px;height:649px}
.values h2{position:absolute;width:1200px;top:49px;text-align:center;font-size:35px;font-weight:700;color:var(--ink)}
.values .intro{position:absolute;width:1200px;top:112px;text-align:center;font-size:15px;line-height:30px}
.value{position:absolute;color:var(--green);font-size:17px;font-weight:500;line-height:27px}
.value.left{text-align:right}

/* reviews */
.reviews{top:3000px;height:590px}
.reviews .photo{left:526px;top:65px;width:600px;height:452px;background:linear-gradient(120deg,#b7b2a8,#e9e2da 45%,#c9a593 70%,#4f6a3b)}
.quote-name{position:absolute;color:var(--green);font-weight:600;font-size:16px}
.pager i{position:absolute;width:11px;height:11px;background:var(--slate)}

/* blog */
.blog{top:3590px;height:619px;background:var(--muted)}
.blog h2{position:absolute;width:1200px;top:55px;text-align:center;font-size:35px;font-weight:700;color:var(--ink)}
.post .photo{width:512px;height:245px;top:125px}
.post .card{position:absolute;top:323px;width:456px;height:240px;background:var(--muted);text-align:center}
.post .date{margin-top:16px;color:var(--green);font-size:18px}
.post h3{font-size:26px;font-weight:600;color:var(--ink);margin-top:2px}
.post .excerpt{font-size:14.5px;line-height:27.5px;margin:6px 12px 0}

/* footer */
.footer{top:4209px;height:325px;background:var(--slate);color:var(--white)}
.footer h4{position:absolute;top:45px;font-size:20px;font-weight:600}
.footer .brand-foot{font-size:24px;top:40px}
.footer .col{position:absolute;top:95px;font-size:14.5px;line-height:38px}
.footer .about{line-height:28px;top:90px;width:250px}
.newsletter-input{position:absolute;left:885px;top:89px;width:241px;height:43px;background:var(--white);color:#777;font-size:14px;padding:12px 16px}
.footer .btn{left:885px;top:148px;width:241px;height:42px}
.copyright{position:absolute;left:0;top:251px;width:1200px;height:74px;border-top:1px solid #5b6f72}
.copyright span{position:absolute;left:74px;top:28px;font-size:13px}
.copyright i{position:absolute;top:26px;width:20px;height:20px;border-radius:50%;background:var(--white)}
</style>
</head>
<body>

<header class="topbar">
  <span class="social-dot" style="left:71px"></span>
  <span class="social-dot" style="left:106px"></span>
  <span class="social-dot" style="left:144px"></span>
  <span class="social-dot" style="left:181px"></span>
  <span class="social-dot" style="left:218px"></span>
  <div class="contact" style="left:583px">
    <svg width="14" height="16" viewBox="0 0 14 16"><path d="M3 1l3 3-2 2c1 2 3 4 5 5l2-2 3 3-2 3C6 15 0 9 1 3z" fill="#ffa000"/></svg>
    1800 -555-0142
  </div>
  <div class="contact" style="left:771px">
    <svg width="16" height="12" viewBox="0 0 16 12"><rect width="16" height="12" fill="#ffa000"/><path d="M0 0l8 6 8-6" stroke="#fff" stroke-width="1.5" fill="none"/></svg>
    hello@veltrana-swiss.ch
  </div>
  <div class="lang"><i></i>EN ⌄</div>
</header>

<header class="nav">
  <div class="brand">Veltrana Swiss AG</div>
  <nav class="menu">
    <a class="active" style="left:353px">Home</a>
    <a style="left:442px">About Us</a>
    <a style="left:553px">Services</a>
    <a style="left:661px">Why Choose Us</a>
    <a style="left:823px">Blog</a>
    <a style="left:900px">Testimonials</a>
    <a style="left:1040px">Contact Us</a>
  </nav>
</header>

<section class="hero">
  <div class="photo" role="img" aria-label="Woman wearing a face mask shopping in a supermarket aisle with a trolley"></div>
  <h1>Veltrana Swiss AG</h1>
  <p>We are a Swiss based start up company, trading<br>Natural &amp; Health food ingredients</p>
  <div class="btn">Read More</div>
  <span class="dot"></span>
</section>

<section class="welcome">
  <div class="photo" role="img" aria-label="Shop assistant showing a supplement jar to a customer in a health store"></div>
  <svg class="abs" style="left:526px;top:123px" width="674" height="405" viewBox="0 0 674 405"><polygon points="0,0 674,0 674,405 81,357" fill="#fff"/></svg>
  <h2 style="left:618px;top:158px">Welcome to Veltrana Swiss AG</h2>
  <p class="body-text abs" style="left:615px;top:212px;width:515px">Sed ut perspiciatis unde omnis iste natus error sit voluptatem accusantium doloremque laudantium, totam rem aperiam, eaque ipsa quae ab illo inventore veritatis et quasi architecto beatae vitae dicta sunt explicabo. Nemo enim ipsam voluptatem quia voluptas sit aspernatur aut odit aut fugit.</p>
  <div class="btn" style="left:615px;top:393px;width:165px;height:44px">Read More</div>
</section>

<section class="split" style="top:1385px">
  <div class="panel" style="left:0;width:614px"></div>
  <div class="photo" style="left:614px;top:0;width:586px;height:482px;background:linear-gradient(180deg,#6d5a4d,#d69a3b 40%,#c75b2c 60%,#8bb450 85%,#4d6a3a)" role="img" aria-label="Supermarket shelves stocked with colourful juice and drink bottles"></div>
  <h2 style="left:79px;top:97px">What We Do</h2>
  <p class="body-text" style="left:77px;top:151px;width:520px">Sed ut perspiciatis unde omnis iste natus error sit voluptatem accusantium doloremque laudantium, totam rem aperiam, eaque ipsa quae ab illo inventore veritatis et quasi architecto beatae vitae dicta sunt explicabo. Nemo enim ipsam voluptatem quia voluptas sit aspernatur aut odit aut fugit.</p>
  <div class="btn" style="left:77px;top:332px;width:165px;height:44px">Read More</div>
</section>

<section class="values">
  <h2>Our Values</h2>
  <p class="intro">Sed ut perspiciatis unde omnis iste natus error sit voluptatem accusantium doloremque laudantium,<br>totam rem aperiam, eaque ipsa quae ab illo inventore.</p>
  <svg class="abs" style="left:0;top:0" width="1200" height="649" viewBox="0 0 1200 649">
    <g stroke="#3e5558" stroke-width="1.5" fill="none">
      <polyline points="444,248 480,248 500,290"/>
      <line x1="391" y1="353" x2="480" y2="353"/>
      <polyline points="444,457 480,457 500,415"/>
      <polyline points="756,248 720,248 700,290"/>
      <line x1="806" y1="353" x2="716" y2="353"/>
      <polyline points="756,457 720,457 700,415"/>
    </g>
    <circle cx="598" cy="350" r="118" fill="#f7ad98" stroke="#3e5558" stroke-width="2"/>
    <g fill="#3e5558">
      <circle cx="405" cy="248" r="39"/><circle cx="352" cy="353" r="39"/><circle cx="405" cy="457" r="39"/>
      <circle cx="795" cy="248" r="39"/><circle cx="845" cy="353" r="39"/><circle cx="795" cy="457" r="39"/>
    </g>
    <g fill="none" stroke="#fff" stroke-width="2">
      <path d="M390 255q15 12 30 -4M398 246q7-16 14 0"/>
      <rect x="338" y="345" width="28" height="18" rx="3"/><path d="M344 345v-8h16v8"/>
      <rect x="392" y="445" width="26" height="24"/><path d="M392 457h26M405 445v24"/>
      <circle cx="795" cy="243" r="12"/><path d="M789 243l4 4 8-8"/>
      <circle cx="845" cy="353" r="13"/><circle cx="845" cy="353" r="5"/>
      <rect x="783" y="446" width="14" height="22"/><circle cx="804" cy="452" r="7"/>
    </g>
  </svg>
  <div class="abs" role="img" aria-label="Illustration of fresh fruits and vegetables bursting from a bowl" style="left:522px;top:277px;width:150px;height:150px;border-radius:50%;background:radial-gradient(circle,#f6e0d6 0%,#e88f75 55%,#f7ad98 75%)"></div>
  <div class="value left" style="left:100px;top:218px;width:242px">Sourcing of natural and<br>health ingredients</div>
  <div class="value left" style="left:90px;top:323px;width:202px">Health &amp;<br>Nutritional Health</div>
  <div class="value left" style="left:60px;top:420px;width:282px">High Quality Standard in<br>term of products and logistic<br>services</div>
  <div class="value" style="left:857px;top:218px">Trust<br>and reliability</div>
  <div class="value" style="left:904px;top:323px">Flexibility &amp; speed<br>to market</div>
  <div class="value" style="left:857px;top:420px">Technical advice for the<br>development of new<br>products</div>
  <div class="btn" style="left:516px;top:532px;width:165px;height:47px">Read More</div>
</section>

<section class="split" style="top:2516px">
  <div class="photo" style="left:0;top:0;width:585px;height:482px;background:linear-gradient(110deg,#d9d3c8,#f2efe8 40%,#e7e4de 65%,#b8b2a6)" role="img" aria-label="Two food industry workers in white coats and hairnets shaking hands in a warehouse"></div>
  <div class="panel" style="left:585px;width:615px"></div>
  <h2 style="left:633px;top:98px">Why Choose Us</h2>
  <p class="body-text" style="left:630px;top:152px;width:520px">Sed ut perspiciatis unde omnis iste natus error sit voluptatem accusantium doloremque laudantium, totam rem aperiam, eaque ipsa quae ab illo inventore veritatis et quasi architecto beatae vitae dicta sunt explicabo. Nemo enim ipsam voluptatem quia voluptas sit aspernatur aut odit aut fugit.</p>
  <div class="btn" style="left:630px;top:330px;width:165px;height:45px">Read More</div>
</section>

<section class="reviews">
  <div class="photo" role="img" aria-label="Woman drinking a green juice through a straw beside a fresh salad"></div>
  <svg class="abs" style="left:526px;top:50px" width="150" height="480" viewBox="0 0 150 480"><polygon points="0,0 150,0 150,64 81,422 81,480 0,480" fill="#fff"/><polygon points="0,0 148,65 81,422 0,422" fill="#fff"/></svg>
  <h2 style="left:75px;top:166px">Customer Reviews</h2>
  <p class="body-text abs" style="left:73px;top:220px;width:500px">“ Sed ut perspiciatis unde omnis iste natus error sit voluptatem accusantium doloremque laudantium, totam rem aperiam, eaque ipsa quae ab illo inventore veritatis et quasi architecto beatae vitae dicta sunt explicabo...”</p>
  <div class="quote-name" style="left:73px;top:351px">-Name Heading</div>
  <div class="pager">
    <i style="left:73px;top:407px;background:var(--orange)"></i>
    <i style="left:99px;top:407px"></i>
    <i style="left:126px;top:407px"></i>
    <i style="left:152px;top:407px"></i>
  </div>
</section>

<section class="blog">
  <h2>Latest Blog Posts</h2>
  <article class="post">
    <div class="photo" style="left:74px;background:linear-gradient(120deg,#6b4a2f,#d7b48c 40%,#f1e6d4 55%,#c7823e 80%,#8a5a2d)" role="img" aria-label="Two women laughing while shopping for fresh produce at a market stall"></div>
    <div class="card" style="left:104px">
      <div class="date">Apr28, 2022</div>
      <h3>Sed ut perspiciatis unde</h3>
      <p class="excerpt">Natus error sit voluptatem accusantium doloremque laudantium, totam rem aperiam, eaque ipsa quae ab illo inventore veritatis et quasi.</p>
    </div>
    <div class="btn" style="left:250px;top:516px;width:162px;height:45px">Read More</div>
  </article>
  <article class="post">
    <div class="photo" style="left:615px;background:linear-gradient(120deg,#cfcfd1,#f4f4f4 45%,#c4c8cc 70%,#a07f86)" role="img" aria-label="Worker in protective suit inspecting bottles on a production line"></div>
    <div class="card" style="left:645px">
      <div class="date">Apr28, 2022</div>
      <h3>Sed ut perspiciatis unde</h3>
      <p class="excerpt">Natus error sit voluptatem accusantium doloremque laudantium, totam rem aperiam, eaque ipsa quae ab illo inventore veritatis et quasi.</p>
    </div>
    <div class="btn" style="left:791px;top:516px;width:162px;height:45px">Read More</div>
  </article>
</section>

<footer class="footer">
  <h4 class="brand-foot" style="left:74px">Veltrana Swiss AG</h4>
  <p class="col about" style="left:74px">Sed ut perspiciatis unde omnis iste natus error sit voluptatem accusantium doloremque arc hitecto beatae</p>
  <h4 style="left:357px">Site Map</h4>
  <div class="col" style="left:357px">Home<br>About Us<br>Services<br>Why Choose Us</div>
  <div class="col" style="left:503px">Blog<br>Testimonials<br>Contact Us</div>
  <h4 style="left:660px">Resources</h4>
  <div class="col" style="left:660px">Sed ut perspiciatis<br>Unde omnis iste<br>Natus error sit volu<br>Ptatem accus</div>
  <h4 style="left:885px">Newsletter Sign Up</h4>
  <div class="newsletter-input">Email Address</div>
  <div class="btn">Subscribe</div>
  <div class="copyright">
    <span>Copyright ©2022 Veltrana Swiss AG. All rights reserved</span>
    <i style="left:930px"></i><i style="left:970px"></i><i style="left:1015px"></i><i style="left:1060px"></i><i style="left:1104px"></i>
  </div>
</footer>

</body>
</html>
```